Brell Stone Company Business Cards

Front and Back Business Card - logo and text setup - cool design. I need workable photoshop or illustrator files so I can setup each employee card with design that is created
Updates

Hi everyone, thank you for the great entries. Please no more white and blue cards - there are so many already - black and silver only now please. thanks!

Target Market(s)

Construction Industry - Facility Managers

Industry/Entity Type

Construction

Contact Information for Business Card

I really like contemporary simplistic looks - clean neat....not opposed to seeing some black backrounds

Requirements
Must have
• Logo/website address with design on front only - www.brellstone-example.com (logo attached)
• Back:
• Name/Title/Company Address/Phone/email address
Nice to have
• Cool design
Should not have
• Nothing gimmicky like Fire or Water - since we are a Fire Protection company - it has all been done

```html
<!DOCTYPE html>
<html lang="en">
<head>
<meta charset="utf-8">
<title>Brell Stone Company – Business Card</title>
<link rel="stylesheet" href="https://fonts.googleapis.com/css2?family=Lato:wght@400;700;900&display=swap">
<style>
  :root {
    --stage: #4f5d5c;
    --card: #0a0b0d;
    --silver: #c3c8cd;
    --silver-light: #eef0f2;
    --steel: #7e868e;
    --graphite: #9aa1a8;
  }
  html, body {
    margin: 0;
    padding: 0;
    width: 1200px;
    height: 1200px;
    overflow: hidden;
    background: var(--stage);
    font-family: "Lato", sans-serif;
  }
  .card {
    position: absolute;
    width: 900px;
    height: 540px;
    background: var(--card);
    overflow: hidden;
  }
  .card--front { left: 152px; top: 49px; }
  .card--back  { left: 150px; top: 613px; }

  .swoosh {
    position: absolute;
    left: 0; top: 0;
    width: 900px; height: 540px;
  }
  .swoosh__outer  { fill: var(--silver); }
  .swoosh__light  { fill: var(--silver-light); }
  .swoosh__inner  { fill: var(--steel); }
  .swoosh__mask   { fill: var(--card); }

  .contact { position: absolute; left: 77px; top: 0; }
  .contact__name {
    position: absolute; top: 72px; left: 0;
    margin: 0;
    font-size: 38px; font-weight: 700; line-height: 1.2;
    color: var(--silver-light); white-space: nowrap;
  }
  .contact__title {
    position: absolute; top: 114px; left: 0;
    margin: 0;
    font-size: 26px; font-weight: 400; line-height: 1.2;
    color: var(--graphite); white-space: nowrap;
  }
  .rule {
    position: absolute; left: 0; height: 4px;
    background: var(--steel);
  }
  .rule--title { top: 147px; width: 354px; }
  .rule--address { top: 258px; width: 376px; }
  .contact__address {
    position: absolute; top: 197px; left: 0;
    margin: 0;
    font-size: 22px; line-height: 27px;
    color: var(--silver); white-space: nowrap; font-style: normal;
  }
  .contact__line {
    position: absolute; left: -5px;
    display: flex; align-items: center; gap: 10px;
    font-size: 24px; color: var(--silver); white-space: nowrap;
  }
  .contact__line--phone { top: 322px; }
  .contact__line--email { top: 362px; }
  .contact__icon { width: 24px; height: 24px; fill: var(--steel); }

  .wordmark {
    position: absolute;
    margin: 0;
    font-weight: 900;
    color: var(--silver);
    white-space: nowrap;
    letter-spacing: -0.01em;
  }
  .wordmark--front { left: 528px; top: 236px; font-size: 50px; line-height: 1; }
  .wordmark--back {
    left: 0; right: 0; top: 222px;
    text-align: center; font-size: 72px; line-height: 1;
  }

  .web-band {
    position: absolute; left: 0; top: 425px;
    width: 900px; height: 40px;
    background: var(--silver);
    display: flex; align-items: center; justify-content: center;
  }
  .web-band__url {
    font-size: 22px; font-weight: 700;
    color: var(--card);
    letter-spacing: 0.32em;
    white-space: nowrap;
  }
</style>
</head>
<body>

<section class="card card--front">
  <svg class="swoosh" viewBox="0 0 900 540" aria-hidden="true">
    <path class="swoosh__outer" d="M0,-2 L406,-2 C535,100 565,330 330,545 L0,545 Z"/>
    <path class="swoosh__light" d="M0,-2 L370,-2 C505,100 535,330 298,545 L0,545 Z"/>
    <path class="swoosh__inner" d="M0,-2 L366,-2 C495,100 525,330 290,545 L0,545 Z"/>
    <path class="swoosh__mask"  d="M0,-2 L326,-2 C455,100 505,300 280,545 L0,545 Z"/>
  </svg>

  <div class="contact">
    <h1 class="contact__name">Dana Whitfield</h1>
    <p class="contact__title">Founder</p>
    <div class="rule rule--title"></div>
    <address class="contact__address">41 Harlow Street<br>Tampa, FL 33602</address>
    <div class="rule rule--address"></div>
    <div class="contact__line contact__line--phone">
      <svg class="contact__icon" viewBox="0 0 24 24" aria-hidden="true">
        <path d="M6.6 10.8a15.1 15.1 0 0 0 6.6 6.6l2.2-2.2c.3-.3.7-.4 1-.2 1.1.4 2.3.6 3.6.6.6 0 1 .4 1 1V20c0 .6-.4 1-1 1A17 17 0 0 1 3 4c0-.6.4-1 1-1h3.5c.6 0 1 .4 1 1 0 1.3.2 2.5.6 3.6.1.3 0 .7-.2 1z"/>
      </svg>
      <span>000-000-000</span>
    </div>
    <div class="contact__line contact__line--email">
      <svg class="contact__icon" viewBox="0 0 24 24" aria-hidden="true">
        <path d="M2 5h20v2l-10 6L2 7z M2 9l10 6 10-6v10H2z"/>
      </svg>
      <span>info@brellmail.com</span>
    </div>
  </div>

  <p class="wordmark wordmark--front">Brell Stone</p>
</section>

<section class="card card--back">
  <p class="wordmark wordmark--back">Brell Stone</p>
  <div class="web-band">
    <span class="web-band__url">www.brellstone-example.com</span>
  </div>
</section>

</body>
</html>
```